Carpet cleaning company focused on high quality needs business cards

We are a growing company that just merged with another company and need to design a new business card. We do both residential as well as commercial cleaning. We do carpet, tile & grout, upholstery, hard floors, and stain & pet odor removal. We treat our customers like family and strive to achieve outstanding results with every job.

```html
<!DOCTYPE html>
<html lang="en">
<head>
<meta charset="utf-8">
<title>Brightwell Floor Care – Business Cards</title>
<link href="https://fonts.googleapis.com/css2?family=Open+Sans:wght@400;600;700&display=swap" rel="stylesheet">
<style>
  :root {
    --red: #e9463d;
    --blue: #1b7cc6;
    --ink: #1b1b1b;
    --white: #ffffff;
    --stage: #dcdde0;
    --mascot-tone: #5f86b0;
  }
  * { box-sizing: border-box; margin: 0; padding: 0; }
  html, body {
    width: 1200px; height: 780px; overflow: hidden;
    background: var(--stage);
    font-family: "Open Sans", Arial, sans-serif;
  }
  .stage {
    width: 1200px; height: 780px;
    display: flex; align-items: center; justify-content: center; gap: 40px;
  }
  .card {
    position: relative; width: 560px; height: 320px; overflow: hidden;
    box-shadow: 0 10px 24px rgba(0,0,0,.22);
  }

  /* Front card */
  .card-front { background: var(--white); }
  .card-front .wave { position: absolute; inset: 0; }
  .front-brand {
    position: absolute; left: 30px; top: 46px; width: 240px;
    display: flex; flex-direction: column; align-items: flex-start; gap: 12px;
  }
  .mascot-area {
    width: 120px; height: 96px; background: var(--mascot-tone);
  }
  .brand-name {
    font-weight: 700; color: var(--ink);
    font-size: 19px; line-height: 1.2; white-space: nowrap;
  }
  .divider {
    position: absolute; left: 282px; top: 42px; width: 1px; height: 130px;
    background: var(--ink);
  }
  .contact { position: absolute; left: 300px; top: 40px; }
  .person-name { font-weight: 700; font-size: 25px; line-height: 1.1; }
  .person-name .first { color: var(--blue); }
  .person-name .last { color: var(--red); }
  .person-title { font-size: 14px; font-weight: 600; color: var(--ink); margin: 2px 0 16px; }
  .contact-list { list-style: none; }
  .contact-list li {
    display: flex; align-items: center; gap: 8px;
    font-size: 12.5px; color: var(--ink); margin-bottom: 5px;
  }
  .contact-list svg { width: 14px; height: 14px; flex: none; }
  .address {
    position: absolute; right: 22px; bottom: 18px;
    color: var(--white); font-size: 13px; font-weight: 600; letter-spacing: .3px;
  }

  /* Back card */
  .card-back { background: var(--red); }
  .back-top {
    position: absolute; left: 40px; top: 34px; display: flex; align-items: center; gap: 24px;
  }
  .back-panel {
    width: 170px; height: 150px; background: var(--white); position: relative;
  }
  .back-panel .mascot-fill {
    position: absolute; left: 28px; top: 14px; width: 114px; height: 122px;
    background: var(--mascot-tone);
  }
  .back-brand {
    font-weight: 700; color: var(--ink);
    font-size: 27px; line-height: 1.2; white-space: nowrap;
  }
  .services {
    position: absolute; left: 24px; right: 24px; bottom: 26px; text-align: center; color: var(--white);
  }
  .services-heading {
    display: flex; align-items: center; gap: 10px;
    font-weight: 700; font-size: 14px; letter-spacing: .5px; margin-bottom: 8px;
  }
  .services-heading::before, .services-heading::after {
    content: ""; flex: 1; height: 1px; background: var(--white);
  }
  .services p { font-size: 13px; font-weight: 600; line-height: 1.6; white-space: nowrap; }
  .dot { display: inline-block; width: 7px; height: 7px; border-radius: 50%; background: var(--white); margin: 0 5px 2px; }
</style>
</head>
<body>
<main class="stage">

  <section class="card card-front" aria-label="Business card front">
    <svg class="wave" viewBox="0 0 560 320" preserveAspectRatio="none" aria-hidden="true">
      <path d="M0 320 C180 300 380 255 560 172 L560 320 Z" fill="var(--blue)"/>
      <path d="M0 320 C180 304 380 262 560 182 L560 320 Z" fill="var(--red)"/>
    </svg>

    <div class="front-brand">
      <div class="mascot-area" role="img" aria-label="Cartoon mascot of a cleaner holding a steam wand"></div>
      <div class="brand-name">Brightwell Floor Care</div>
    </div>

    <div class="divider"></div>

    <div class="contact">
      <h1 class="person-name"><span class="first">Lena</span> <span class="last">Marvik</span></h1>
      <p class="person-title">Managing Director</p>
      <ul class="contact-list">
        <li>
          <svg viewBox="0 0 24 24"><path fill="var(--blue)" d="M6.6 10.8a15 15 0 0 0 6.6 6.6l2.2-2.2a1 1 0 0 1 1-.25 11.4 11.4 0 0 0 3.6.57 1 1 0 0 1 1 1V20a1 1 0 0 1-1 1A17 17 0 0 1 3 4a1 1 0 0 1 1-1h3.5a1 1 0 0 1 1 1c0 1.250.2 2.450.57 3.6a1 1 0 0 1-.25 1z"/></svg>
          (555) 014-2270
        </li>
        <li>
          <svg viewBox="0 0 24 24"><rect x="2" y="5" width="20" height="14" rx="2" fill="var(--blue)"/><path d="M3 6l9 7 9-7" stroke="var(--white)" stroke-width="1.8" fill="none"/></svg>
          hello@brightwellcare.com
        </li>
        <li>
          <svg viewBox="0 0 24 24"><circle cx="12" cy="12" r="10" fill="var(--blue)"/><path d="M2 12h20M12 2c3 3 3 17 0 20M12 2c-3 3-3 17 0 20" stroke="var(--white)" stroke-width="1.4" fill="none"/></svg>
          www.brightwellcare.com
        </li>
      </ul>
    </div>

    <p class="address">418 Alder Ridge Rd. Suite 120 Fairhaven, TX 75010</p>
  </section>

  <section class="card card-back" aria-label="Business card back">
    <div class="back-top">
      <div class="back-panel">
        <div class="mascot-fill" role="img" aria-label="Cartoon mascot of a cleaner holding a steam wand"></div>
      </div>
      <div class="back-brand">Brightwell Floor Care</div>
    </div>

    <div class="services">
      <h2 class="services-heading">OUR SERVICES</h2>
      <p><span class="dot"></span>Both residential as well as commercial cleaning</p>
      <p><span class="dot"></span>Carpet <span class="dot"></span>Tile &amp; grout <span class="dot"></span>Upholstery <span class="dot"></span>Hard floors <span class="dot"></span>Stain &amp; pet odor removal</p>
    </div>
  </section>

</main>
</body>
</html>
```